Start-Up für Training, Coaching & Consulting sucht modernes Webdesign!
Zielgruppe
Wer ist TAVI Training, Coaching & Consulting?
Wir führen Führungskräftetrainings durch, machen Privatkunden für Bewerbungen fit und unterstützen Unternehmen mit Verkaufstrainings. Wir entwickeln Persönlichkeiten im Coaching. Wir beraten Unternehmen und helfen ihnen dabei, ihre Geschäftsabläufe und Prozesse zu optimieren. Dabei steht unsere hohe Qualität im Mittelpunkt - gemeinsam mit unseren kreativen Trainingsmethoden. Unser Background (Diplom-Kaufleute und geprüfte Trainer) bietet dafür die passende Ausgangslage.
Was bedeutet TAVI?
Tavi ist Maori und bdeutet Kreis/Spirale. Er symbolisiert einen wachsenden Silberfarn und steht für persönliche Entwicklung und Entfaltung. Der Tavi ist einerseits unser Namensgeber und unser Logo, andererseits steht der Tavi aber auch für unsere Werte: Denn wir wollen unseren Kunden dabei helfen zu wachsen und sich weiterzuentwickeln - und dies auf eine hochqualitative und seriöse Art und Weise ohne den Eindruck von Esoterik oder Erlebnispädagogik zu vermitteln.
Aufgabenstellung
Modernes Design, das unsere Philosophie widerspiegelt: Wir möchten unseren Kunden auf seriöse und hochqualitative Weise weiterentwickeln. Wir stehen für nachhaltigen Lernerfolg, kreative Trainingsmethoden, Abwechslung, Spaß am Lernen, Qualität, Kompetenz, Fachwissen und Dynamik.
Layout:
1) Header: QMSR geprüfter Trainer, Menüpunkte (siehe Architektur)
2) Banner
3) 3 Teaser (Training, Coaching, Consulting) + Header + 2-3 Zeilen Text (+Icons)
>>> Sichtbarer Bereich auf Homepage: Menü, Banner, Teaser
4) "Warum Sie uns wählen sollten": 5 bullet points ohne weiteren Text
5) "Aus unserem Blog": Frame für 3 Blogartikel + Bild + Datum + Header + 2-3 Zeilen Text
6) Alle drei QMSR Logos
7) Footer: Click Us (quick links), Contact Us (Adresse), Follow Us (Pinnwald, ZOLP, Kontaktor)
8) Copyright + Impressum
>>> Das Design soll klar sein, aber nicht zu kantig. Vielmehr sollen abgerundete Ecken und dynamische Elemente genutzt werden.
Architektur:
3 Ebenen:
1) Homepage
2) TAVI, Training, Coaching, Consulting, für Trainer, Kundenstimmen/Referenzen, Kontakt
3) noch zu bestimmende Produktdetailseiten
Texte werden noch erstellt, Layout kann ggf. mit Platzhaltertext gefüllt werden.
Bildmaterial: Logo und vorhandenes Imagebild werden zur Verfügung gestellt. Bilder können ggf. gekauft werden. Vorschläge erwünscht.
Corporate colors:
grün: #a2c61b + monochromatic colors
http://www.tintoskop.de/a2c61b
grau: #474747 + monochromatic colors
http://www.tintoskop.de/474747

```html
<!DOCTYPE html>
<html lang="en">
<head>
<meta charset="utf-8">
<title>TAVI Training, Coaching &amp; Consulting</title>
<link href="https://fonts.googleapis.com/css2?family=Lato:wght@300;400;700&display=swap" rel="stylesheet">
<style>
:root{
  --green:#a2c61b;
  --green-dark:#3f6e1c;
  --green-deep:#1f3f10;
  --grey:#474747;
  --grey-dark:#2b2b2b;
  --grey-bar:#3d3d3d;
  --text:#5a5a5a;
  --text-light:#9a9a9a;
  --bg-light:#f5f5f5;
  --white:#ffffff;
}
*{margin:0;padding:0;box-sizing:border-box}
html,body{width:1168px;height:1200px;overflow:hidden;background:var(--white)}
body{font-family:'Lato',sans-serif;font-weight:300;color:var(--text);position:relative}
.abs{position:absolute}
/* top bar */
.topbar{left:0;top:0;width:1168px;height:18px;background:var(--grey-bar);color:#ddd;font-size:8.5px;font-weight:400}
.topbar .item{top:4px;display:flex;align-items:center;gap:4px}
.topbar .sep{left:303px;top:4px;width:1px;height:10px;background:#777}
/* header */
.header{left:0;top:18px;width:1168px;height:61px;background:#f7f7f7;border-bottom:1px solid #e6e6e6}
.brand{left:237px;top:27px;display:flex;align-items:center;gap:5px}
.brand-dot{width:14px;height:14px;border-radius:50%;background:var(--green)}
.brand-name{font-size:27px;font-weight:700;color:var(--grey);letter-spacing:1px;line-height:1}
.brand-tag{left:237px;top:62px;font-size:5.5px;font-weight:400;color:var(--grey)}
.social-top{right:237px;top:31px;font-size:7px;font-weight:400;color:#5a6fa8;display:flex;gap:6px}
.nav{right:237px;top:57px;display:flex;gap:26px;font-size:9.5px;font-weight:400;color:var(--grey)}
.nav .active{color:var(--green)}
.nav-underline{left:444px;top:76px;width:52px;height:2px;background:var(--green)}
/* hero */
.hero{left:0;top:79px;width:1168px;height:231px;background:radial-gradient(ellipse at 35% 40%,#6fa33a 0%,#3f7a22 35%,var(--green-deep) 75%,#142b0a 100%)}
.hero-title{left:247px;top:142px;font-size:23px;font-weight:400;color:var(--green)}
.hero-text{left:248px;top:177px;width:320px;font-size:10.5px;line-height:13px;font-weight:400;color:var(--white)}
.hero-btn{left:248px;top:215px;width:143px;height:27px;background:var(--green);color:var(--white);font-size:12px;font-weight:400;display:flex;align-items:center;justify-content:center}
/* cards */
.card{top:347px;width:224px;height:269px;background:var(--white);box-shadow:0 1px 3px rgba(0,0,0,.2)}
.card-img{width:224px;height:151px}
.img-training{background:linear-gradient(160deg,#dfe6ea,#9aa9b4 60%,#6f7f8c)}
.img-coaching{background:linear-gradient(160deg,#e4eaee,#a9b4bc 55%,#3a3f48)}
.img-consulting{background:linear-gradient(120deg,#cdd9e2,#b6c3cd 50%,#4a4f57)}
.card-title{margin:8px 0 0 10px;font-size:15.5px;font-weight:300;color:var(--grey)}
.card-text{margin:5px 8px 0 10px;font-size:9.2px;line-height:13.4px;color:var(--text-light)}
.read-more{margin:8px 0 0 10px;font-size:10.5px;color:var(--green);font-weight:400}
.read-more span{font-size:6px;margin-left:4px}
/* why + blog */
.band{left:0;top:655px;width:1168px;height:267px;background:var(--bg-light)}
.section-title{font-size:15px;font-weight:300;color:var(--grey)}
.why-item{left:247px;display:flex;gap:14px;width:320px}
.why-item p{font-size:9.2px;line-height:13.4px;color:var(--text-light)}
.divider{left:581px;top:730px;width:1px;height:166px;background:#e2e2e2}
.blog-item{left:605px;display:flex;gap:10px}
.blog-thumb{width:98px;height:49px;border-radius:2px;background:radial-gradient(ellipse at 45% 55%,#8fbf4a,#3d7a22 55%,#1f3f10)}
.blog-title{font-size:12.5px;color:var(--grey);font-weight:300;margin-top:2px}
.blog-date{font-size:9px;font-style:italic;color:var(--grey);margin-top:3px}
.blog-text{font-size:9px;color:var(--text-light);margin-top:3px}
.blog-text em{font-style:normal;color:var(--green)}
/* badges */
.badge{top:947px;height:32px}
/* footer */
.footer{left:0;top:1005px;width:1168px;height:195px;background:var(--grey-dark);color:#c9c9c9}
.foot-title{top:1033px;font-size:11px;font-weight:400;color:var(--white)}
.foot-links{left:304px;top:1060px;font-size:9px;font-weight:400;line-height:19px;list-style:none}
.foot-links li span{font-size:5px;margin-right:7px;vertical-align:1px}
.foot-links .current{color:var(--green)}
.contact-row{left:531px;display:flex;gap:7px;font-size:9px;font-weight:400;line-height:13px}
.follow{left:785px;top:1064px;font-size:11px;font-weight:700;color:var(--white);display:flex;gap:12px}
.foot-brand{left:785px;top:1093px;font-size:28px;font-weight:700;color:#8a8a8a;letter-spacing:1px}
.foot-tag{left:786px;top:1128px;font-size:5.5px;color:#8a8a8a;font-weight:400}
.foot-line{left:237px;top:1175px;width:694px;height:1px;background:#555}
.foot-small{top:1181px;font-size:8px;font-weight:400}
</style>
</head>
<body>

<div class="abs topbar">
  <div class="abs item" style="left:237px">
    <svg width="7" height="8" viewBox="0 0 10 10"><path d="M2 0l2 2.5-1.2 1.2c.6 1.3 1.6 2.3 2.9 2.9L7 5.4 9.5 7.4 8.4 9.8C4 9.6.4 6 .2 1.6z" fill="var(--green)"/></svg>
    31 4620 118
  </div>
  <div class="abs sep"></div>
  <div class="abs item" style="left:310px">
    <svg width="9" height="7" viewBox="0 0 12 9"><rect width="12" height="9" fill="var(--green)"/><path d="M0 0l6 5 6-5" stroke="var(--grey-bar)" fill="none"/></svg>
    hello@tavi.one
  </div>
  <div class="abs item" style="left:893px">English <span style="font-size:6px;margin-left:6px">▼</span></div>
</div>

<div class="abs header"></div>
<div class="abs brand"><div class="brand-dot"></div><div class="brand-name">TAVI</div></div>
<div class="abs brand-tag">Training · Coaching · Consulting</div>
<div class="abs social-top"><span>Pinnwald</span><span>ZOLP</span><span>Kontaktor</span></div>
<nav class="abs nav">
  <span class="active">HOME</span><span>ABOUT US</span><span>TRAINING</span><span>COACHING</span><span>CONSULTANT</span><span>JOBS</span><span>CONTACT US</span>
</nav>
<div class="abs nav-underline"></div>

<div class="abs hero" role="img" aria-label="Close-up photo of an unfurling green fern frond"></div>
<h1 class="abs hero-title">WELCOME TEXT</h1>
<p class="abs hero-text">Lorem Ipsum is simply dummy text of the printing and typesetting industry. Lorem Ipsum has been the industry's standard.</p>
<div class="abs hero-btn">CONTACT US</div>

<div class="abs card" style="left:237px">
  <div class="card-img img-training" role="img" aria-label="Photo of a trainer presenting at a flipchart to a seated group"></div>
  <h2 class="card-title">TRAINING</h2>
  <p class="card-text">Lorem Ipsum is simply dummy text of the printing and typesetting industry. Lorem Ipsum has been the industry's standard dummy text ever since the 1500s, when an unknown printer took a</p>
  <div class="read-more">Read More<span>►</span></div>
</div>
<div class="abs card" style="left:471px">
  <div class="card-img img-coaching" role="img" aria-label="Photo of business people talking at a meeting table"></div>
  <h2 class="card-title">COACHING</h2>
  <p class="card-text">Lorem Ipsum is simply dummy text of the printing and typesetting industry. Lorem Ipsum has been the industry's standard dummy text ever since the 1500s, when an unknown printer took a</p>
  <div class="read-more">Read More<span>►</span></div>
</div>
<div class="abs card" style="left:706px">
  <div class="card-img img-consulting" role="img" aria-label="Photo of a consultant in a suit standing in a conference room"></div>
  <h2 class="card-title">CONSULTING</h2>
  <p class="card-text">Lorem Ipsum is simply dummy text of the printing and typesetting industry. Lorem Ipsum has been the industry's standard dummy text ever since the 1500s, when an unknown printer took a</p>
  <div class="read-more">Read More<span>►</span></div>
</div>

<div class="abs band"></div>
<h2 class="abs section-title" style="left:247px;top:688px">WHY CHOOSE US</h2>
<h2 class="abs section-title" style="left:603px;top:688px">AUS UNSEREM BLOG</h2>

<div class="abs why-item" style="top:724px"><svg width="12" height="12" viewBox="0 0 12 12"><path d="M1 6l3 4 7-9" stroke="var(--green)" stroke-width="1.3" fill="none"/></svg><p>Lorem Ipsum is simply dummy text of the printing and typesetting industry. Lorem Ipsum has been the industry's standard dummy text</p></div>
<div class="abs why-item" style="top:760px"><svg width="12" height="12" viewBox="0 0 12 12"><path d="M1 6l3 4 7-9" stroke="var(--green)" stroke-width="1.3" fill="none"/></svg><p>Lorem Ipsum is simply dummy text of the printing and typesetting industry. Lorem Ipsum has been the industry's standard dummy text</p></div>
<div class="abs why-item" style="top:796px"><svg width="12" height="12" viewBox="0 0 12 12"><path d="M1 6l3 4 7-9" stroke="var(--green)" stroke-width="1.3" fill="none"/></svg><p>Lorem Ipsum is simply dummy text of the printing and typesetting industry. Lorem Ipsum has been the industry's standard dummy text</p></div>
<div class="abs why-item" style="top:832px"><svg width="12" height="12" viewBox="0 0 12 12"><path d="M1 6l3 4 7-9" stroke="var(--green)" stroke-width="1.3" fill="none"/></svg><p>Lorem Ipsum is simply dummy text of the printing and typesetting industry. Lorem Ipsum has been the industry's standard dummy text</p></div>
<div class="abs why-item" style="top:868px"><svg width="12" height="12" viewBox="0 0 12 12"><path d="M1 6l3 4 7-9" stroke="var(--green)" stroke-width="1.3" fill="none"/></svg><p>Lorem Ipsum is simply dummy text of the printing and typesetting industry. Lorem Ipsum has been the industry's standard dummy text</p></div>

<div class="abs divider"></div>

<div class="abs blog-item" style="top:728px">
  <div class="blog-thumb" role="img" aria-label="Fern frond thumbnail"></div>
  <div><div class="blog-title">LOREM IPSUM</div><div class="blog-date">17 December 2015 by Admin</div><div class="blog-text">Lorem Ipsum is simply dummy text of ... <em>read more</em></div></div>
</div>
<div class="abs blog-item" style="top:789px">
  <div class="blog-thumb" role="img" aria-label="Fern frond thumbnail"></div>
  <div><div class="blog-title">LOREM IPSUM</div><div class="blog-date">15 December 2015 by Admin</div><div class="blog-text">Lorem Ipsum is simply dummy text of ... <em>read more</em></div></div>
</div>
<div class="abs blog-item" style="top:850px">
  <div class="blog-thumb" role="img" aria-label="Fern frond thumbnail"></div>
  <div><div class="blog-title">LOREM IPSUM</div><div class="blog-date">9 December 2015 by Admin</div><div class="blog-text">Lorem Ipsum is simply dummy text of ... <em>read more</em></div></div>
</div>

<div class="abs badge" style="left:381px;width:24px;background:#1f5fb5"></div>
<div class="abs badge" style="left:522px;width:114px;background:#c9c9c9;border-radius:2px"></div>
<div class="abs badge" style="left:716px;width:24px;background:#cfcfcf"></div>

<div class="abs footer"></div>
<h3 class="abs foot-title" style="left:304px">CLICK US</h3>
<h3 class="abs foot-title" style="left:531px">CONTACT US</h3>
<h3 class="abs foot-title" style="left:785px">FOLLOW US</h3>
<ul class="abs foot-links">
  <li class="current"><span>►</span>Lorem Ipsum</li>
  <li><span>►</span>Lorem Ipsum</li>
  <li><span>►</span>Lorem Ipsum</li>
  <li><span>►</span>Lorem Ipsum</li>
  <li><span>►</span>Lorem Ipsum</li>
</ul>
<div class="abs contact-row" style="top:1061px">
  <svg width="7" height="9" viewBox="0 0 8 10" style="margin-top:2px"><path d="M4 0a3.5 3.5 0 0 0-3.5 3.5C.5 6 4 10 4 10s3.5-4 3.5-6.5A3.5 3.5 0 0 0 4 0z" fill="#aaa"/><circle cx="4" cy="3.5" r="1.2" fill="var(--grey-dark)"/></svg>
  <div>Lindenweg 14<br>D-60311 Mainfeld</div>
</div>
<div class="abs contact-row" style="top:1095px">
  <svg width="9" height="7" viewBox="0 0 12 9" style="margin-top:3px"><rect width="12" height="9" fill="#aaa"/><path d="M0 0l6 5 6-5" stroke="var(--grey-dark)" fill="none"/></svg>
  <div>hello@tavi.one</div>
</div>
<div class="abs contact-row" style="top:1119px">
  <svg width="8" height="8" viewBox="0 0 10 10" style="margin-top:3px"><path d="M2 0l2 2.5-1.2 1.2c.6 1.3 1.6 2.3 2.9 2.9L7 5.4 9.5 7.4 8.4 9.8C4 9.6.4 6 .2 1.6z" fill="#aaa"/></svg>
  <div>+49 1520 4620 118</div>
</div>
<div class="abs follow"><span>Pinnwald</span><span>Kontaktor</span><span>ZOLP</span></div>
<div class="abs foot-brand">TAVI</div>
<div class="abs foot-tag">Training · Coaching · Consulting</div>
<div class="abs foot-line"></div>
<div class="abs foot-small" style="left:246px">Impressum</div>
<div class="abs foot-small" style="right:247px">Copyright © 2015 tavi.one</div>

</body>
</html>
```